Locksmith Business Cards

My father-in-law is in need of new business cards for his locksmith business and I need to impress him. Kindly help me out!

You can see the previous business card attached. It is a family run business in North Wales.

No individual names on the cards.

Key Things to Feature:
- The words "Prompt", "Local", "Reliable" (as you can see under the logo on the website)
- 24h Emergency Service
- Covering All of North Wales, the Wirral and Chester
- The color blue
- A key or a lock would be interesting (similar to the ones that come up when you google locksmith business card)

Optional (only if design includes bullet points, like the example below):
https://imgvaultcdn.net/samples/208314/55172/55172_3904821_208314_image.jpg
- Residential / Commercial / Automotive
- Alarms & Cameras
- Key Cutting & Safes

https://www.brynhafod-locksmiths.co.uk/

Industry/Entity Type

Locksmith

Contact Information for Business Card

01632 960 418
07700 900 362
brynhafodlocksmiths@mailvane.com
Brynhafod Locksmiths, The Willow Barn, 7 Tannery Rd., Llandudno LL99 4QX
www.brynhafod-locksmiths.co.uk

Requirements
Must have
• - The words "Prompt", "Local", "Reliable" (as you can see under the logo on the website)
• - 24h Emergency Service
• - Covering All of North Wales, the Wirral and Chester
Nice to have
• - A key or a lock would be interesting (similar to the ones that come up when you google locksmith business card)

```html
<!DOCTYPE html>
<html lang="en">
<head>
<meta charset="utf-8">
<title>Brynhafod Locksmiths – Business Card</title>
<link href="https://fonts.googleapis.com/css2?family=Open+Sans:wght@400;600;700&display=swap" rel="stylesheet">
<style>
  :root {
    --page-bg: #2a2b2e;
    --card-bg: #1d1e21;
    --card-shade: #26272b;
    --brand-blue: #2f3f94;
    --text-main: #f2f2f2;
    --text-soft: #c9c9cc;
    --rule: #6a6b70;
  }
  * { box-sizing: border-box; margin: 0; padding: 0; }
  html, body {
    width: 1200px; height: 1108px; overflow: hidden;
    background: var(--page-bg);
    font-family: "Open Sans", Arial, sans-serif;
  }
  .sheet {
    width: 1200px; height: 1108px;
    display: flex; justify-content: center; align-items: center; gap: 60px;
  }
  .card {
    width: 420px; height: 660px;
    background: var(--card-bg);
    border-radius: 22px;
    box-shadow: 0 18px 40px rgba(0,0,0,.45);
    position: relative; overflow: hidden;
    color: var(--text-main);
    text-align: center;
  }
  /* front */
  .brand {
    margin-top: 110px;
    display: flex; align-items: center; justify-content: center; gap: 14px;
  }
  .brand-mark {
    width: 46px; height: 46px; border-radius: 6px;
    background: var(--brand-blue);
  }
  .brand-name {
    color: var(--brand-blue);
    font-weight: 700; font-size: 31px; line-height: 1.05;
    text-transform: uppercase; text-align: left; letter-spacing: .5px;
  }
  .tagline {
    margin-top: 16px;
    font-weight: 700; font-size: 15px; letter-spacing: .6px;
  }
  .address {
    margin-top: 42px; font-size: 16px; line-height: 1.45;
  }
  .rule {
    width: 190px; height: 1px; background: var(--rule);
    margin: 14px auto;
  }
  .contacts { font-size: 16px; line-height: 1.45; }
  .contacts b { font-weight: 700; }
  .coverage { font-size: 16px; line-height: 1.4; }
  .coverage strong { font-weight: 700; display: block; font-size: 16.5px; }
  /* back */
  .pattern-field {
    position: absolute; left: 0; top: 0; width: 100%; height: 440px;
    background: linear-gradient(180deg, var(--card-shade) 0%, var(--card-bg) 100%);
  }
  .back-brand {
    position: absolute; left: 0; right: 0; top: 456px;
    display: flex; align-items: center; justify-content: center; gap: 10px;
    font-weight: 700; font-size: 20px; text-transform: uppercase; letter-spacing: .5px;
  }
  .back-brand .dot {
    width: 18px; height: 18px; border-radius: 50%; background: var(--text-main);
  }
  .services {
    position: absolute; left: 0; right: 0; top: 516px;
    list-style: none; font-size: 17px; line-height: 1.5;
  }
</style>
</head>
<body>
<main class="sheet">
  <section class="card card-front">
    <div class="brand">
      <span class="brand-mark"></span>
      <span class="brand-name">Brynhafod<br>Locksmiths</span>
    </div>
    <p class="tagline">PROMPT. LOCAL. RELIABLE</p>
    <p class="address">Brynhafod Locksmiths,<br>The Willow Barn, 7,<br>Tannery Rd., Llandudno LL99 4QX</p>
    <div class="rule"></div>
    <p class="contacts">
      <b>P:</b> 01632 960 418<br>
      <b>M:</b> 07700 900 362<br>
      <b>E:</b> brynhafodlocksmiths@mailvane.com<br>
      www.brynhafod-locksmiths.co.uk
    </p>
    <div class="rule"></div>
    <p class="coverage"><strong>24H EMERGENCY SERVICE</strong>Covering All of North Wales,<br>the Wirral and Chester</p>
  </section>

  <section class="card card-back">
    <div class="pattern-field" role="img" aria-label="Faint repeating brand pattern on the dark card face"></div>
    <div class="back-brand"><span class="dot"></span>Brynhafod Locksmiths</div>
    <ul class="services">
      <li>Residential / Commercial / Automotive</li>
      <li>Alarms &amp; Cameras</li>
      <li>Key Cutting &amp; Safes</li>
    </ul>
  </section>
</main>
</body>
</html>
```